LM-Steuerberatung WordPress Site fully implemented (tax advisor)

Hello!
I need a little Wordpress Site for my newly founded Tax-Advisor Company.
I am a one-man Office advising in the area of Crypto-Currency.
PLEASE only provide a Design, if you can also Implement a WP-Site afterwards on an existing Webspace.

Please find the Content and Website-Description in the attached Document

Language for the Website is German (for now)

Target Market(s)

Tax-Advisory (specialized in Crypto Currency)

Coding

Coded - Design and coding required

Number of Pages Required

5+ page

Font styles to use
Sans Serif

Requirements
Must have
• Wordpress Implementation afterwards - Details according to attached Project Information Document

```html
<!DOCTYPE html>
<html lang="de">
<head>
<meta charset="utf-8">
<title>LM-Steuerberatung</title>
<link rel="stylesheet" href="https://fonts.googleapis.com/css2?family=Montserrat:wght@500;600;700&display=swap">
<style>
  :root {
    --navy: #1b2a45;
    --ink: #2b3344;
    --white: #ffffff;
    --band: rgba(190, 194, 202, 0.78);
    --hero-dark: #17223a;
    --hero-mid: #3a4a68;
  }
  * { box-sizing: border-box; margin: 0; padding: 0; }
  html, body { width: 1200px; height: 849px; overflow: hidden; }
  body { font-family: "Montserrat", Arial, sans-serif; background: var(--white); position: relative; }

  .site-header { position: absolute; top: 0; left: 0; width: 1200px; height: 119px; background: var(--white); }
  .brand { position: absolute; left: 111px; top: 43px; display: flex; align-items: center; gap: 10px;
           font-weight: 700; font-size: 20px; color: var(--navy); letter-spacing: 0.5px; }
  .brand-mark { width: 16px; height: 16px; background: var(--navy); }
  .main-nav { position: absolute; right: 111px; top: 49px; display: flex; gap: 28px;
              font-size: 15px; font-weight: 600; color: var(--ink); letter-spacing: 0.2px; }
  .main-nav span { display: flex; align-items: center; gap: 5px; }
  .caret { width: 0; height: 0; border-left: 5px solid transparent; border-right: 5px solid transparent; border-top: 6px solid var(--ink); }

  .hero { position: absolute; top: 119px; left: 0; width: 1200px; height: 653px; overflow: hidden; }
  .hero-image { position: absolute; inset: 0;
    background: radial-gradient(ellipse at 30% 35%, #4b5a78 0%, transparent 55%),
                radial-gradient(ellipse at 85% 55%, #3b5a8e 0%, transparent 50%),
                linear-gradient(180deg, var(--hero-mid) 0%, var(--hero-dark) 70%, #24365a 100%); }
  .hero-content { position: absolute; top: 0; left: 0; width: 1200px; text-align: center; color: var(--white); }
  .hero-kicker { position: absolute; top: 168px; width: 100%; font-size: 30px; font-weight: 500; letter-spacing: 0.5px; }
  .hero-title { position: absolute; top: 204px; width: 100%; font-size: 42px; font-weight: 700; }
  .hero-lead { position: absolute; top: 273px; width: 100%; font-size: 19px; font-weight: 700; line-height: 28px; }
  .hero-button { position: absolute; top: 353px; left: 457px; width: 286px; height: 51px;
                 border: 2px solid var(--white); border-radius: 26px; display: flex; align-items: center; justify-content: center;
                 font-size: 14px; font-weight: 600; }
  .slider-arrow { position: absolute; top: 298px; width: 59px; height: 59px; }
  .slider-arrow.prev { left: 37px; }
  .slider-arrow.next { left: 1100px; }
  .ribbon { position: absolute; top: 495px; left: 200px; width: 800px; height: 68px; }
  .ribbon-text { position: absolute; top: 495px; left: 0; width: 1200px; height: 68px; display: flex;
                 align-items: center; justify-content: center; color: var(--white); font-size: 19px; font-weight: 700; }

  .site-footer { position: absolute; top: 772px; left: 0; width: 1200px; height: 77px; background: var(--navy);
                 color: var(--white); font-family: Arial, Helvetica, sans-serif; font-size: 16px; text-align: center; padding-top: 29px; }
</style>
</head>
<body>
  <header class="site-header">
    <div class="brand"><span class="brand-mark"></span>LM STEUERBERATUNG</div>
    <nav class="main-nav">
      <span>HEIM</span>
      <span>LEISTUNGEN <i class="caret"></i></span>
      <span>ÜBER MICH</span>
      <span>KONTAKT</span>
      <span>IMPRESSUM</span>
    </nav>
  </header>

  <section class="hero">
    <div class="hero-image" role="img" aria-label="Hände an einem Laptop mit digitalem Netzwerkmuster im Vordergrund"></div>
    <div class="hero-content">
      <p class="hero-kicker">WILLKOMMEN BEI</p>
      <h1 class="hero-title">LM-STEUERBERATUNG!</h1>
      <p class="hero-lead">IHREM SPEZIALISTEN BEI ALLEN STEUERLICHEN THEMEN RUND UM<br>EINKÜNFTE &amp; VERMÖGEN AUS KRYPTO-ASSETS</p>
      <div class="hero-button">WEITER ZU UNSEREN LEISTUNGEN</div>
    </div>
    <svg class="slider-arrow prev" viewBox="0 0 59 59"><circle cx="29.5" cy="29.5" r="28" fill="none" stroke="#fff" stroke-width="2"/><path d="M33 22 L26 29.5 L33 37" fill="none" stroke="#fff" stroke-width="2.5"/></svg>
    <svg class="slider-arrow next" viewBox="0 0 59 59"><circle cx="29.5" cy="29.5" r="28" fill="none" stroke="#fff" stroke-width="2"/><path d="M26 22 L33 29.5 L26 37" fill="none" stroke="#fff" stroke-width="2.5"/></svg>
    <svg class="ribbon" viewBox="0 0 800 68" preserveAspectRatio="none"><polygon points="0,0 800,0 788,34 800,68 0,68 24,34" fill="var(--band)"/></svg>
    <div class="ribbon-text">DANN MELDE ICH EINFACH MEINEN HAUPTWOHNSITZ IN ÖSTERREICH AB</div>
  </section>

  <footer class="site-footer">©2022 LM-Steuerberatung Alle Rechte vorbehalten.</footer>
</body>
</html>
```